Venture Capital firm needs modern business cards

We are a Venture Capital firm within financial services/Asset management. The industry generally has basic business cards with black, blue and maybe green/yellow design elements.
Our firm has a four-colour swoosh logo. We are based in London and want to stand out, just a little bit!, from the crowd. Our company is called LORV Investments and the 'C' stands for collaboration thus using makerswarm is a natural portal for our business card design competition. Our logo came via makerswarm too!
We use 'Venture Partner in Asset Management' as our tagline and this is Trademark registered. We operate in a conservative industry and we should not overstep our mark. The logo is colorful as it is and therefore the rest of the design should not be too fanciful.
The objective is twofold: make our logo element stick and memorable with our audience, whilst representing a conservative yet young image.
Updates
The Business Card obviously needs a field for Name, Surname, Job Title, Adress fields: Street, City, Postcode, Country, telefone and cell number, website address, etc.
We have uploaded the ai file. We trust that these are OK. If not, please advise.
Reason: We have have been busy with a client engagement. We will set the project as Guaranteed in return for the troubles we cause. Apologies for the confusion.
Thank you all for these great and creative design suggestions. The team is very happy with a number of your ideas! We will be in touch tomorrow to give individual feedback before the project closes on Friday. We look forward to working with some of you to narrow down your creations. Thank you, LORV Investments team.
All,
Target Market(s)
Financial Services Professionals, Investors, Media, 35-70 years, mainly male, well educated
Industry/Entity Type
Conservative
Requirements
Must have
- We must make use of our logo and potential tagline 'Venture Partner in Asset Management' as we are establishing a new Brand and new company in the market.
We can use 'LORV', 'LORV Investments', and 'LORV Investments'+tagline 'Venture Partner in Asset Management' or simply the four-colour swoosh plus the name of the company as part of the text. (see files)
All design elements are available in black or grey-scale if required. (grey scale swoosh attached).
Due to regulation we must have the following wording on the card in small print 'LORV Investments is an Appointed Representative of Bramwell Holdings Partnership Limited, which is authorised by the Monetary Oversight Board'.
Nice to have
- We would consider designs that make use of different printing techniques such embossing/debossing, UV spot etc.
We attach our colour palette in the files section for your reference.
Should not have
- The font we use for our company name is 'EXO' so do not use a font style that clashes with the corporate fonts, please.
Do not use other design elements than the ones we provide in the file library as part of this project.

```html
<!DOCTYPE html>
<html lang="en">
<head>
<meta charset="utf-8">
<title>LORV Investments – Business Card</title>
<link href="https://fonts.googleapis.com/css2?family=Exo:wght@500&family=Roboto+Condensed:wght@700&family=Roboto:wght@400&display=swap" rel="stylesheet">
<style>
  :root {
    --page-bg: #e9e9ea;
    --card-bg: #f7f7f5;
    --card-shadow: rgba(0, 0, 0, 0.18);
    --ink: #4a4a4c;
    --ink-soft: #7b7b7e;
    --rule: #c9c9cb;
    --brand-green: #7cc242;
    --brand-mark: #7cc242;
  }
  * { margin: 0; padding: 0; box-sizing: border-box; }
  html, body {
    width: 1200px;
    height: 800px;
    overflow: hidden;
    background: var(--page-bg);
  }
  .canvas {
    position: relative;
    width: 1200px;
    height: 800px;
    display: flex;
    align-items: center;
    justify-content: center;
    gap: 60px;
  }
  .card {
    position: relative;
    width: 510px;
    height: 300px;
    background: var(--card-bg);
    box-shadow: 0 6px 18px var(--card-shadow);
  }

  /* Back of card */
  .card-back .brand {
    position: absolute;
    left: 0;
    width: 272px;
    top: 150px;
    display: flex;
    align-items: center;
    justify-content: center;
    gap: 8px;
  }
  .brand-dot {
    width: 22px;
    height: 22px;
    border-radius: 50%;
    background: var(--brand-mark);
    flex: none;
  }
  .brand-name {
    font-family: "Exo", sans-serif;
    font-weight: 500;
    font-size: 20px;
    color: var(--ink);
    letter-spacing: 0.3px;
    white-space: nowrap;
  }
  .divider {
    position: absolute;
    left: 272px;
    top: 42px;
    width: 1px;
    height: 168px;
    background: var(--rule);
  }
  .contact {
    position: absolute;
    left: 273px;
    right: 0;
    top: 28px;
    text-align: center;
    font-family: "Roboto", sans-serif;
    color: var(--ink-soft);
  }
  .person-name {
    font-family: "Roboto Condensed", sans-serif;
    font-weight: 700;
    font-size: 21px;
    color: var(--brand-green);
    letter-spacing: 0.3px;
    line-height: 1;
  }
  .person-title {
    font-size: 11px;
    margin-top: 3px;
  }
  .contact-item {
    margin-top: 10px;
    font-size: 11px;
    line-height: 1.35;
  }
  .contact-item svg {
    display: block;
    margin: 0 auto 3px;
    fill: none;
    stroke: var(--ink-soft);
    stroke-width: 1.4;
  }
  .legal {
    position: absolute;
    left: 0;
    right: 0;
    bottom: 14px;
    text-align: center;
    font-family: "Roboto", sans-serif;
    font-size: 6.5px;
    color: var(--ink-soft);
    padding: 0 40px;
  }

  /* Front of card */
  .card-front .brand-front {
    position: absolute;
    inset: 0;
    display: flex;
    align-items: center;
    justify-content: center;
    gap: 16px;
  }
  .brand-front .brand-dot {
    width: 54px;
    height: 54px;
  }
  .brand-front .brand-name {
    font-size: 52px;
  }
</style>
</head>
<body>
<main class="canvas">

  <section class="card card-back" aria-label="Business card, back">
    <div class="brand">
      <span class="brand-dot"></span>
      <span class="brand-name">LORV Investments</span>
    </div>

    <div class="divider"></div>

    <div class="contact">
      <p class="person-name">MARCUS DELLAWAY</p>
      <p class="person-title">Graphic designer</p>

      <div class="contact-item">
        <svg width="10" height="15" viewBox="0 0 10 15" aria-hidden="true">
          <rect x="1" y="1" width="8" height="13" rx="1.2"/>
          <line x1="4" y1="12" x2="6" y2="12"/>
        </svg>
        +44 20 7946 0123
      </div>

      <div class="contact-item">
        <svg width="14" height="10" viewBox="0 0 14 10" aria-hidden="true">
          <rect x="1" y="1" width="12" height="8"/>
          <polyline points="1,1 7,6 13,1"/>
        </svg>
        http://www.lorvinvest.net
      </div>

      <div class="contact-item">
        <svg width="10" height="14" viewBox="0 0 10 14" aria-hidden="true">
          <path d="M5 13 C2 9 1 7 1 5 A4 4 0 0 1 9 5 C9 7 8 9 5 13 Z"/>
          <circle cx="5" cy="5" r="1.4"/>
        </svg>
        48 Kestrel Row<br>Fenwick Vale
      </div>
    </div>

    <p class="legal">LORV Investments is an Appointed Representative of Bramwell Holdings Partnership Limited, which is authorised by the Monetary Oversight Board</p>
  </section>

  <section class="card card-front" aria-label="Business card, front">
    <div class="brand-front">
      <span class="brand-dot"></span>
      <span class="brand-name">LORV</span>
    </div>
  </section>

</main>
</body>
</html>
```